Tallowmere Air Business Card Design

Design new, 2 sides, business cards for a residential and light commercial heating, air conditioning contractor.

Target Market(s)

Homeowners, small businesses

Industry/Entity Type

Business

Contact Information for Business Card

Dominic Westerhall
Phone - 862-415-2736
Email
Address - PO box 518
Brightwater NJ 07912
Website - www.HarborBreezeLLC.example

Requirements
Must have
• logo, company colors, standard size with no die cut, so I can use nova stamp

```html
<!DOCTYPE html>
<html lang="en">
<head>
<meta charset="utf-8">
<title>Tallowmere Air Business Card</title>
<link rel="stylesheet" href="https://fonts.googleapis.com/css2?family=Roboto:wght@400;500&family=Roboto+Slab:wght@700&display=swap">
<style>
  :root {
    --backdrop: #e6e6e6;
    --maroon: #7e2528;
    --maroon-dark: #6a1c20;
    --gold: #e2b21c;
    --name-yellow: #f4b81e;
    --cream: #f5e2a6;
    --orange: #e08a1e;
    --red: #c8331f;
    --white: #ffffff;
  }
  * { box-sizing: border-box; margin: 0; padding: 0; }
  html, body { width: 1200px; height: 576px; overflow: hidden; }
  body {
    background: var(--backdrop);
    font-family: "Roboto", Arial, sans-serif;
    position: relative;
  }
  .card {
    position: absolute;
    top: 138px;
    background: var(--maroon);
    overflow: hidden;
  }
  .card--front { left: 81px; width: 485px; height: 294px; }
  .card--back { left: 602px; width: 481px; height: 291px; }

  .brand-name {
    position: absolute;
    font-family: "Roboto", Arial, sans-serif;
    font-weight: 500;
    color: var(--cream);
    white-space: nowrap;
    transform: translate(-50%, -50%);
    letter-spacing: 0.5px;
  }
  .card--front .brand-name { left: 243px; top: 134px; font-size: 38px; }
  .card--back .brand-name { left: 364px; top: 82px; font-size: 24px; }

  .service-band {
    position: absolute;
    left: 0; top: 249px;
    width: 100%; height: 22px;
    background: var(--gold);
    color: var(--maroon-dark);
    font-size: 12.5px;
    line-height: 22px;
    text-align: center;
  }

  .holder-name {
    position: absolute;
    left: 23px; top: 30px;
    font-family: "Roboto Slab", "Rockwell", serif;
    font-weight: 700;
    font-size: 19px;
    color: var(--name-yellow);
  }
  .holder-title {
    position: absolute;
    left: 23px; top: 60px;
    font-size: 11px;
    color: var(--white);
  }

  .contact-list {
    position: absolute;
    left: 24px; top: 160px;
    list-style: none;
  }
  .contact-list li {
    display: flex;
    align-items: center;
    height: 17px;
    font-size: 12.5px;
    color: var(--white);
  }
  .contact-list svg { width: 12px; height: 12px; margin-right: 11px; flex: none; }

  .wave { position: absolute; left: 0; top: 0; }

  .service-list {
    position: absolute;
    right: 19px; top: 214px;
    list-style: none;
    text-align: right;
    color: var(--maroon-dark);
    font-size: 12.5px;
    font-weight: 500;
    line-height: 16px;
  }
  .service-list li { position: relative; padding-right: 13px; }
  .service-list li::after {
    content: "«";
    position: absolute; right: 0; top: 0;
  }
  .service-list li .cont { display: block; }
</style>
</head>
<body>

<section class="card card--front" aria-label="Business card front">
  <div class="brand-name">Tallowmere Air</div>
  <div class="service-band">Residential &amp; Light Commercial Heating &nbsp;• Air Conditioning Contractor</div>
</section>

<section class="card card--back" aria-label="Business card back">
  <svg class="wave" width="481" height="291" viewBox="0 0 481 291" aria-hidden="true">
    <path d="M0 272 C150 280 260 262 340 222 C400 192 440 180 481 178 L481 291 L0 291 Z" fill="var(--orange)"/>
    <path d="M0 242 C80 250 170 262 262 268 C180 273 80 271 0 268 Z" fill="var(--red)"/>
    <path d="M38 256 C160 268 260 250 330 212 C390 178 440 164 481 160" fill="none" stroke="var(--cream)" stroke-width="5"/>
  </svg>

  <div class="holder-name">Dominic Westerhall</div>
  <div class="holder-title">Managing Director</div>
  <div class="brand-name">Tallowmere Air</div>

  <ul class="contact-list">
    <li>
      <svg viewBox="0 0 12 12" aria-hidden="true"><path d="M1 4 Q6 0 11 4 L9 5 L8 3.5 L4 3.5 L3 5 Z M2.5 6 L9.5 6 L10.5 11 L1.5 11 Z" fill="var(--name-yellow)"/></svg>
      862-415-2736
    </li>
    <li>
      <svg viewBox="0 0 12 12" aria-hidden="true"><rect x="1" y="2.5" width="10" height="7" fill="var(--name-yellow)"/><path d="M1 2.5 L6 7 L11 2.5" fill="none" stroke="var(--maroon)" stroke-width="1"/></svg>
      info@TallowmereAirLLC.example
    </li>
    <li>
      <svg viewBox="0 0 12 12" aria-hidden="true"><path d="M6 11.5 C3 7.5 2 6 2 4.5 A4 4 0 0 1 10 4.5 C10 6 9 7.5 6 11.5 Z" fill="var(--name-yellow)"/><circle cx="6" cy="4.5" r="1.6" fill="var(--maroon)"/></svg>
      PO box 518 Brightwater NJ 07912
    </li>
    <li>
      <svg viewBox="0 0 12 12" aria-hidden="true"><circle cx="6" cy="6" r="5" fill="var(--name-yellow)"/><path d="M1 6 H11 M6 1 V11 M6 1 C3.5 4 3.5 8 6 11 M6 1 C8.5 4 8.5 8 6 11" fill="none" stroke="var(--maroon)" stroke-width="0.7"/></svg>
      TallowmereAirLLC.example
    </li>
  </ul>

  <ul class="service-list">
    <li>Air Conditioning<span class="cont">Contractor</span></li>
    <li>Residential and Light<span class="cont">Commercial Heating</span></li>
  </ul>
</section>

</body>
</html>
```